Communication and Marketing agency needs a new presentation card

We are a group of communication and marketing agencies specialized in companies that are in the logistics and industrial sector. The head agency is TELVANO Grupo and the group consists of 4 agencies: TELVANO Media, TELVANO Digital, TELVANO Research and DifundeEnPantalla. We hace 4 offices in Spain (Madrid, Barcelona, Valencia and Murcia). We are looking for a clean and attractive design that transmits our experience, brand presence in the market and knowledge to those who receive the card.It has to maintain the colors of the logo that is attached.
Target Market(s)
logistics and industrial sector
Marketing department
Contact Information for Business Card
Clean and attractive design

```html
<!DOCTYPE html>
<html lang="es">
<head>
<meta charset="utf-8">
<title>TELVANO Grupo – Business Card</title>
<link href="https://fonts.googleapis.com/css2?family=Open+Sans:wght@400;600;700&display=swap" rel="stylesheet">
<style>
  :root {
    --brand-red: #b01c28;
    --ink-grey: #4a4a4a;
    --soft-grey: #6b6b6b;
    --paper: #ffffff;
    --backdrop: #dcdcdc;
  }
  * { margin: 0; padding: 0; box-sizing: border-box; }
  html, body {
    width: 1200px; height: 900px; overflow: hidden;
    background: var(--backdrop);
    font-family: "Open Sans", Arial, sans-serif;
  }
  .stage {
    position: relative; width: 1200px; height: 900px;
  }
  .card {
    position: absolute; left: 290px;
    width: 620px; height: 354px;
    border-radius: 34px;
    box-shadow: 0 6px 18px rgba(0,0,0,0.18);
    overflow: hidden;
  }
  /* Front */
  .card--front { top: 70px; background: var(--brand-red); color: var(--paper); }
  .card--front .wordmark {
    position: absolute; left: 0; right: 0; top: 120px;
    text-align: center; font-weight: 600;
  }
  .wordmark__name { font-size: 58px; letter-spacing: 2px; line-height: 1; }
  .wordmark__sub { display: block; font-size: 26px; margin-top: 4px; margin-left: 200px; }
  .offices {
    position: absolute; left: 0; right: 0; bottom: 40px;
    text-align: center; font-size: 15px; letter-spacing: 1.5px;
  }
  /* Back */
  .card--back { top: 476px; background: var(--paper); }
  .card--back .wordmark {
    position: absolute; right: 44px; top: 40px;
    color: var(--brand-red); font-weight: 600; text-align: right;
  }
  .card--back .wordmark__sub { margin-left: 0; color: var(--brand-red); }
  .agencies {
    position: absolute; right: 40px; top: 150px;
    display: grid; grid-template-columns: auto auto; gap: 16px 22px;
    justify-items: end;
  }
  .agency {
    color: var(--soft-grey); font-size: 16px; font-weight: 600; letter-spacing: 0.5px;
  }
  .agency--accent { color: var(--brand-red); }
  .contact {
    position: absolute; left: 44px; bottom: 36px;
    color: var(--ink-grey);
  }
  .contact__name {
    color: var(--brand-red); font-weight: 700; font-size: 22px; letter-spacing: 0.5px;
  }
  .contact__role { font-size: 16px; margin-bottom: 6px; }
  .contact__line {
    display: flex; align-items: center; gap: 8px;
    font-size: 16px; line-height: 22px;
  }
  .contact__icon { width: 13px; height: 13px; fill: var(--brand-red); flex: none; }
</style>
</head>
<body>
<main class="stage">
  <section class="card card--front" aria-label="Card front">
    <div class="wordmark">
      <span class="wordmark__name">TELVANO</span>
      <span class="wordmark__sub">Grupo</span>
    </div>
    <p class="offices">MADRID, BARCELONA, VALENCIA, MURCIA</p>
  </section>

  <section class="card card--back" aria-label="Card back">
    <div class="wordmark">
      <span class="wordmark__name">TELVANO</span>
      <span class="wordmark__sub">Grupo</span>
    </div>

    <div class="agencies">
      <span class="agency">TELVANO Research</span>
      <span class="agency">TELVANO Digital</span>
      <span class="agency agency--accent">TELVANO Media</span>
      <span class="agency agency--accent">DifundeEnPantalla</span>
    </div>

    <div class="contact">
      <p class="contact__name">ADRIÁN BELTRÁN</p>
      <p class="contact__role">Managing Director</p>
      <p class="contact__line">
        <svg class="contact__icon" viewBox="0 0 16 16" aria-hidden="true"><path d="M3 2h3l1.5 4-2 1.2a9 9 0 0 0 3.3 3.3L10 8.5l4 1.5v3a1.5 1.5 0 0 1-1.6 1.5A12 12 0 0 1 1.5 3.6 1.5 1.5 0 0 1 3 2z"/></svg>
        044-555 210 347
      </p>
      <p class="contact__line">
        <svg class="contact__icon" viewBox="0 0 16 16" aria-hidden="true"><path d="M4 0h8a1.5 1.5 0 0 1 1.5 1.5v13A1.5 1.5 0 0 1 12 16H4a1.5 1.5 0 0 1-1.5-1.5v-13A1.5 1.5 0 0 1 4 0zm0 2v11h8V2z"/></svg>
        044-555 210 347
      </p>
      <p class="contact__line">
        <svg class="contact__icon" viewBox="0 0 16 16" aria-hidden="true"><path d="M0 3h16v10H0zm1.5 1.5v.4L8 9l6.5-4.1v-.4z"/></svg>
        info@telvanogrupo.es
      </p>
      <p class="contact__line">
        <svg class="contact__icon" viewBox="0 0 16 16" aria-hidden="true"><circle cx="8" cy="8" r="7.5"/></svg>
        www.telvanogrupo.es
      </p>
    </div>
  </section>
</main>
</body>
</html>
```